Business Card for Professional Photographer

I'm looking for an eye catching modern clean design that compliments my logo/ website fonts & colours.
I specialise in architecture, corporate & commercial photography so I'm marketing to professional clients rather than portrait / wedding clients.

I would prefer to not have a solid black design.

My logo brand guide is as follows :

Main front font. : Reislust
Main font colour : #fff
Slogan front font : Ubuntu Bold
Monogram front font : Venti Medium
Container colour : #fff

I need print ready files in pdf .png & .eps formats.

Included in the files below are some screen grabs as reference to font & colours etc.

```html
<!DOCTYPE html>
<html lang="en">
<head>
<meta charset="utf-8">
<title>Clearline Studio – Business Card</title>
<link href="https://fonts.googleapis.com/css2?family=Ubuntu:wght@300;400;500;700&display=swap" rel="stylesheet">
<style>
  :root {
    --backdrop: #1b1c1e;
    --card-top: #3b3d41;
    --card-bottom: #2b2d30;
    --card-edge: #a27a44;
    --gold: #c99d60;
    --white: #ffffff;
    --text-light: #e8e8e8;
    --divider: #85878b;
  }
  * { margin: 0; padding: 0; box-sizing: border-box; }
  html, body {
    width: 1200px;
    height: 900px;
    overflow: hidden;
    background: var(--backdrop);
    font-family: "Ubuntu", sans-serif;
  }
  .stage {
    width: 1200px;
    height: 900px;
    display: flex;
    flex-direction: column;
    align-items: center;
    justify-content: center;
    gap: 40px;
  }
  .card {
    position: relative;
    width: 660px;
    height: 377px;
    background: linear-gradient(160deg, var(--card-top) 0%, var(--card-bottom) 100%);
    border-bottom: 4px solid var(--card-edge);
    box-shadow: 0 10px 28px rgba(0,0,0,0.5);
  }

  /* Front */
  .card-front {
    display: flex;
    align-items: center;
    justify-content: center;
    padding-bottom: 30px;
  }
  .brand {
    display: flex;
    align-items: center;
    gap: 22px;
  }
  .brand-dot {
    width: 18px;
    height: 18px;
    border-radius: 50%;
    background: var(--gold);
  }
  .brand-text { display: flex; flex-direction: column; gap: 6px; }
  .brand-name {
    color: var(--white);
    font-weight: 300;
    font-size: 30px;
    letter-spacing: 5px;
    text-transform: uppercase;
  }
  .brand-tagline {
    color: var(--white);
    font-weight: 700;
    font-size: 9px;
    letter-spacing: 2.6px;
  }

  /* Back */
  .card-back {
    display: flex;
    align-items: center;
    justify-content: center;
    padding-top: 20px;
  }
  .contact-block {
    display: flex;
    align-items: stretch;
    gap: 22px;
  }
  .identity {
    text-align: right;
    display: flex;
    flex-direction: column;
  }
  .person-name {
    color: var(--gold);
    font-weight: 500;
    font-size: 24px;
    margin-bottom: 4px;
  }
  .person-role {
    color: var(--text-light);
    font-weight: 700;
    font-size: 16px;
    margin-bottom: 4px;
  }
  .person-address {
    color: var(--text-light);
    font-size: 16px;
    line-height: 1.3;
  }
  .divider {
    width: 1px;
    background: var(--divider);
  }
  .channels {
    list-style: none;
    display: flex;
    flex-direction: column;
    justify-content: center;
    gap: 4px;
    padding-top: 8px;
  }
  .channel {
    display: flex;
    align-items: center;
    gap: 10px;
    color: var(--text-light);
    font-size: 18px;
  }
  .channel svg { width: 15px; height: 15px; fill: var(--gold); flex: none; }
</style>
</head>
<body>
<main class="stage">
  <section class="card card-front">
    <div class="brand">
      <span class="brand-dot"></span>
      <div class="brand-text">
        <span class="brand-name">Clearline Studio</span>
        <span class="brand-tagline">Architecture Corporate Commercial</span>
      </div>
    </div>
  </section>

  <section class="card card-back">
    <div class="contact-block">
      <div class="identity">
        <p class="person-name">Daniel Reyes</p>
        <p class="person-role">President</p>
        <p class="person-address">4120 Harbor View Road<br>Juneau, Alaska 99801</p>
      </div>
      <span class="divider"></span>
      <ul class="channels">
        <li class="channel">
          <svg viewBox="0 0 16 16"><path d="M3.6 1.2l2.3 2.6-1.2 1.8c.9 1.9 2.4 3.5 4.3 4.5l1.8-1.2 2.6 2.3-1.4 2.3C7.3 13.6 2.4 8.7 1.4 2.6z"/></svg>
          555-214-0186
        </li>
        <li class="channel">
          <svg viewBox="0 0 16 16"><path d="M4.5 0.5h7a1 1 0 0 1 1 1v13a1 1 0 0 1-1 1h-7a1 1 0 0 1-1-1v-13a1 1 0 0 1 1-1zm.5 2v9.5h6V2.5zm3 10.3a.8.8 0 1 0 0 1.6.8.8 0 0 0 0-1.6z"/></svg>
          555-390-0172
        </li>
        <li class="channel">
          <svg viewBox="0 0 16 16"><path d="M1 3.5h14v9H1zm1.4 1.2L8 8.6l5.6-3.9z"/></svg>
          info@clearlinestudio.com
        </li>
        <li class="channel">
          <svg viewBox="0 0 16 16"><circle cx="8" cy="8" r="7"/></svg>
          www.clearlinestudio.com
        </li>
      </ul>
    </div>
  </section>
</main>
</body>
</html>
```